Business Card Design for Property Development Company Director

I am looking for a professional and unforgettable business card design for our Director of our Property Development Company.
Please see attached .pptx file to find out what information to include. You don't have to follow the exact format shown in the file - I am interested to see your creative flair using the information provided.

```html
<!DOCTYPE html>
<html lang="en">
<head>
<meta charset="utf-8">
<title>Harlowe Property Group – Business Card</title>
<link rel="stylesheet" href="https://fonts.googleapis.com/css2?family=Lato:wght@400;700&family=Roboto+Condensed:wght@400&display=swap">
<style>
  :root {
    --backdrop: #b9b9b9;
    --brand-blue: #0b55a3;
    --brand-grey: #5f5f5f;
    --paper: #ffffff;
    --ink: #333333;
  }
  * { margin: 0; padding: 0; box-sizing: border-box; }
  html, body { width: 1200px; height: 802px; overflow: hidden; }
  body {
    background: var(--backdrop);
    position: relative;
    font-family: "Lato", sans-serif;
  }
  .card {
    position: absolute;
    top: 274px;
    width: 443px;
    height: 264px;
    background: var(--paper);
    overflow: hidden;
  }
  .card--front { left: 136px; background: var(--brand-blue); }
  .card--back { left: 624px; }

  .front-panel { position: absolute; inset: 0; }

  .front-details {
    position: absolute;
    right: 30px;
    top: 38px;
    text-align: right;
    color: var(--paper);
  }
  .holder-name { font-size: 16px; font-weight: 700; letter-spacing: -0.2px; line-height: 18px; }
  .holder-role { font-size: 12.5px; line-height: 14px; }
  .contact-list { list-style: none; margin-top: 62px; font-size: 13px; line-height: 16px; }
  .contact-list li { display: flex; justify-content: flex-end; align-items: center; gap: 4px; }
  .contact-list svg { width: 10px; height: 10px; fill: var(--paper); }
  .licence { margin-top: 19px; font-size: 13px; line-height: 16px; }

  .brand-lockup {
    position: absolute;
    left: 88px;
    top: 86px;
    display: flex;
    align-items: center;
    gap: 14px;
    color: var(--brand-grey);
    font-weight: 700;
  }
  .brand-square { width: 56px; height: 56px; background: var(--brand-blue); }
  .brand-name { line-height: 1; }
  .brand-name .primary { display: block; font-size: 34px; letter-spacing: 0.5px; }
  .brand-name .secondary { display: block; font-size: 13px; letter-spacing: 3.6px; margin-top: 4px; }

  .tagline {
    position: absolute;
    top: 158px;
    width: 100%;
    text-align: center;
    font-family: "Roboto Condensed", sans-serif;
    font-size: 11.5px;
    color: #222;
  }
  .divider {
    position: absolute;
    top: 214px;
    left: 65px;
    width: 312px;
    height: 1px;
    background: var(--brand-blue);
  }
  .invite {
    position: absolute;
    top: 222px;
    width: 100%;
    text-align: center;
    font-size: 11.8px;
    color: var(--ink);
  }
</style>
</head>
<body>
  <section class="card card--front">
    <svg class="front-panel" viewBox="0 0 443 264" preserveAspectRatio="none" aria-hidden="true">
      <path d="M0 0 H215 L277 264 H0 Z" fill="#ffffff"/>
    </svg>
    <div class="front-details">
      <p class="holder-name">DANIEL MERCER</p>
      <p class="holder-role">Director</p>
      <ul class="contact-list">
        <li>0400 123 456
          <svg viewBox="0 0 10 10"><path d="M1 3 Q5 0 9 3 L8 4.5 L6.5 4 V3.3 H3.5 V4 L2 4.5 Z M2.5 5 H7.5 L8.5 9 H1.5 Z"/></svg>
        </li>
        <li>daniel@harlowe.com.au
          <svg viewBox="0 0 10 10"><path d="M0.5 2 H9.5 V8 H0.5 Z M1.2 2.6 L5 5.5 L8.8 2.6" stroke="#0b55a3" stroke-width="0.7"/></svg>
        </li>
        <li>www.harlowe.com.au
          <svg viewBox="0 0 10 10"><circle cx="5" cy="5" r="4.5"/><path d="M2.5 3.5 L4.5 3 L5 5 L3.5 6.5 Z M6 6 L7.5 5.5 L7 8 Z" fill="#0b55a3"/></svg>
        </li>
      </ul>
      <p class="licence">Real Estate Lic<br>1234567 &amp; 1234568</p>
    </div>
  </section>

  <section class="card card--back">
    <div class="brand-lockup">
      <span class="brand-square" aria-hidden="true"></span>
      <p class="brand-name">
        <span class="primary">HARLOWE</span>
        <span class="secondary">PROPERTY GROUP</span>
      </p>
    </div>
    <p class="tagline">PROPERTY DEVELOPMENT &amp; SITE ACQUISITION SPECIALISTS</p>
    <div class="divider"></div>
    <p class="invite">Ask me about our INVESTMENT &amp; PARTNERSHIP opportunities</p>
  </section>
</body>
</html>
```